GJ & DW Fencing Pty Ltd

We already have an existing logo created by Pixel Harbour however we have restructured to a company. We would like someone to add Pty Ltd to our business name please.

Colors

Designer to choose only greyscale colors for use in the design.

```html
<!DOCTYPE html>
<html lang="en">
<head>
<meta charset="utf-8">
<title>GJ &amp; DW Fencing Pty Ltd — Business Card</title>
<link rel="stylesheet" href="https://fonts.googleapis.com/css2?family=Lato:wght@400&family=Merriweather:wght@700&display=swap">
<style>
  :root {
    --stage: #b9b9b9;
    --card: #070707;
    --ink: #ffffff;
    --ink-soft: #e9e9e9;
    --shadow: rgba(0,0,0,0.35);
  }
  html, body {
    margin: 0;
    padding: 0;
    width: 1200px;
    height: 802px;
    overflow: hidden;
    background: var(--stage);
  }
  .stage {
    position: relative;
    width: 1200px;
    height: 802px;
  }
  .card {
    position: absolute;
    top: 274px;
    width: 443px;
    height: 264px;
    background: var(--card);
    box-shadow: 2px 3px 6px var(--shadow);
    overflow: hidden;
  }
  .card--front { left: 136px; }
  .card--back { left: 624px; }

  .holder-name {
    position: absolute;
    left: 30px;
    top: 36px;
    margin: 0;
    font-family: "Merriweather", serif;
    font-weight: 700;
    font-size: 20px;
    letter-spacing: 0.3px;
    color: var(--ink);
  }
  .mascot-art {
    position: absolute;
    left: 246px;
    top: 26px;
    width: 188px;
    height: 238px;
    background: var(--ink-soft);
    border-radius: 90px 60px 12px 70px / 90px 60px 12px 90px;
  }
  .contact-list {
    position: absolute;
    left: 28px;
    top: 164px;
    margin: 0;
    padding: 0;
    list-style: none;
    font-family: "Lato", sans-serif;
    font-size: 12.5px;
    color: var(--ink);
  }
  .contact-list li {
    display: flex;
    align-items: center;
    gap: 5px;
    height: 20px;
    white-space: nowrap;
  }
  .contact-list .contact-address { margin-top: 16px; }
  .contact-icon { width: 17px; height: 17px; flex: none; }

  .brand-name {
    position: absolute;
    left: 0;
    right: 0;
    top: 112px;
    margin: 0;
    text-align: center;
    font-family: "Merriweather", serif;
    font-weight: 700;
    font-size: 22px;
    color: var(--ink);
  }
</style>
</head>
<body>
<main class="stage">
  <section class="card card--front" aria-label="Business card front">
    <h1 class="holder-name">TOM ASHCROFT</h1>
    <div class="mascot-art" role="img" aria-label="White illustration of a standing animal mascot"></div>
    <ul class="contact-list">
      <li>
        <svg class="contact-icon" viewBox="0 0 20 20" aria-hidden="true">
          <circle cx="10" cy="10" r="10" fill="#fff"/>
          <path d="M5 8.5c0-1.5 2.3-2.5 5-2.5s5 1 5 2.5v1h-2.3v-1.2H7.3v1.2H5z M7 10.5h6l1 3.5H6z" fill="#070707"/>
        </svg>
        <span>044 5190427</span>
      </li>
      <li>
        <svg class="contact-icon" viewBox="0 0 20 20" aria-hidden="true">
          <circle cx="10" cy="10" r="10" fill="#fff"/>
          <rect x="5" y="6.5" width="10" height="7" fill="#070707"/>
          <path d="M5.5 7l4.5 3.5L14.5 7" stroke="#fff" stroke-width="1" fill="none"/>
        </svg>
        <span>Gjdwfencing@mailbox.com</span>
      </li>
      <li class="contact-address">
        <svg class="contact-icon" viewBox="0 0 20 20" aria-hidden="true">
          <circle cx="10" cy="10" r="10" fill="#fff"/>
          <path d="M10 4a4 4 0 0 0-4 4c0 3 4 8 4 8s4-5 4-8a4 4 0 0 0-4-4z" fill="#070707"/>
          <circle cx="10" cy="8" r="1.5" fill="#fff"/>
        </svg>
        <span>PO Box 418 Kelmscott WA 6111</span>
      </li>
    </ul>
  </section>

  <section class="card card--back" aria-label="Business card back">
    <p class="brand-name">GJ &amp; DW Fencing Pty Ltd</p>
  </section>
</main>
</body>
</html>
```